A Label for an ECO Friendly Spirit Company

Design a label which can be used for vodka and gin (London Dry Gin). It should be Square type Like the Shape File you see in the uploads. KIRO means Kind Inventive Rare and Original. We want a cool and slim label that calls for eco-friendly. We want to use it for our premium
Vodka and our London Dry Gin. Please use the logo and design it in Square Type.

40%vol, 700ml

Target Market(s)

spirits and events

Industry/Entity Type

SPIRITS

Colors
00AB8E
00BBA5
67D7C9
C6EFE9
E9F9F6
59FF00
82FF00
B8FF75
E3FFCB
F4FFEA

Requirements
Must have
• Logo from KIRO, Squaee Shape

```html
<!DOCTYPE html>
<html lang="en">
<head>
<meta charset="utf-8">
<title>KIRO Vodka Label</title>
<link href="https://fonts.googleapis.com/css2?family=Montserrat:wght@500;600;700;800&family=Oswald:wght@500&family=Courgette&display=swap" rel="stylesheet">
<style>
  :root {
    --bg: #ffffff;
    --green-deep: #6e9830;
    --green-mid: #86ad36;
    --green-soft: #a8c93a;
    --lime: #c8f542;
    --pale: #f4ffea;
    --pale-line: #e3ffcb;
    --teal: #00ab8e;
    --text-green: #6f9a32;
  }
  html, body {
    margin: 0;
    padding: 0;
    width: 878px;
    height: 1200px;
    overflow: hidden;
    background: var(--bg);
  }
  .canvas {
    position: relative;
    width: 878px;
    height: 1200px;
  }
  .label {
    position: absolute;
    inset: 0;
    width: 878px;
    height: 1200px;
  }
  .brand-name {
    font-family: "Montserrat", sans-serif;
    font-weight: 600;
    fill: var(--teal);
  }
  .product-name {
    font-family: "Montserrat", sans-serif;
    font-weight: 800;
    fill: var(--text-green);
  }
  .grade {
    font-family: "Courgette", cursive;
    fill: var(--text-green);
  }
  .values-main {
    font-family: "Montserrat", sans-serif;
    font-weight: 600;
    fill: var(--teal);
  }
  .values-sub {
    font-family: "Montserrat", sans-serif;
    font-weight: 500;
    fill: var(--green-soft);
  }
  .spec {
    font-family: "Oswald", sans-serif;
    font-weight: 500;
    font-style: italic;
    fill: var(--text-green);
  }
  .rule {
    stroke: var(--green-mid);
    stroke-width: 1.5;
  }
</style>
</head>
<body>
<main class="canvas">
  <svg class="label" viewBox="0 0 878 1200" xmlns="http://www.w3.org/2000/svg">
    <defs>
      <linearGradient id="band-fill" x1="0" y1="0" x2="0" y2="1">
        <stop offset="0" stop-color="#79a034"/>
        <stop offset="1" stop-color="#a9ca3a"/>
      </linearGradient>
      <linearGradient id="frame-fill" x1="0" y1="0" x2="0" y2="1">
        <stop offset="0" stop-color="#6e9830"/>
        <stop offset="0.5" stop-color="#9cc23a"/>
        <stop offset="1" stop-color="#6e9830"/>
      </linearGradient>
      <linearGradient id="lime-fill" x1="0" y1="0" x2="1" y2="0">
        <stop offset="0" stop-color="#b8ff75"/>
        <stop offset="0.5" stop-color="#a6cf3c"/>
        <stop offset="1" stop-color="#c8f542"/>
      </linearGradient>
    </defs>

    <!-- side band -->
    <rect class="band" x="47" y="442" width="784" height="302" fill="url(#band-fill)"/>

    <!-- diamond frame layers -->
    <polygon points="439,276 771,600 439,922 107,600" fill="url(#frame-fill)"/>
    <polygon points="439,294 753,600 439,904 125,600" fill="#ffffff"/>
    <polygon points="439,304 743,600 439,894 135,600" fill="url(#lime-fill)"/>
    <polygon points="439,314 733,600 439,884 145,600" fill="#ffffff"/>
    <polygon points="439,322 725,600 439,876 153,600" fill="var(--pale)" stroke="var(--pale-line)" stroke-width="3"/>

    <!-- brand mark: plain square beside name -->
    <rect class="brand-square" x="401" y="412" width="76" height="76" rx="10" fill="var(--green-soft)"/>

    <!-- brand name with rules -->
    <line class="rule" x1="262" y1="523" x2="380" y2="523"/>
    <line class="rule" x1="498" y1="523" x2="616" y2="523"/>
    <text class="brand-name" x="439" y="535" font-size="33" text-anchor="middle">KIRO</text>

    <!-- product -->
    <text class="product-name" x="439" y="624" font-size="98" text-anchor="middle" letter-spacing="1">VODKA</text>

    <!-- grade with rules -->
    <line class="rule" x1="284" y1="642" x2="372" y2="642"/>
    <line class="rule" x1="506" y1="642" x2="594" y2="642"/>
    <text class="grade" x="439" y="651" font-size="27" text-anchor="middle">Premium</text>

    <!-- values -->
    <text class="values-main" x="439" y="700" font-size="20" text-anchor="middle">KIND INVENTIVE</text>
    <text class="values-sub" x="439" y="726" font-size="14" text-anchor="middle" letter-spacing="4">RARE AND ORIGINAL</text>

    <!-- specs -->
    <text class="spec" x="439" y="796" font-size="24" text-anchor="middle">40%vol</text>
    <text class="spec" x="439" y="828" font-size="24" text-anchor="middle">700ml</text>
  </svg>
</main>
</body>
</html>
```